Website for BrightlineLabs presentation

We need a new website, ideally as a wordpress there, for BrightlineLabs - we focus on machine learning, big data, data science and data analytics. This website should have two main sections - team presentation, introduction and offered services as static pages, and a blog section.

Target Market(s)

Companies which would like to hire the consultants for data science

Industry/Entity Type

Data Service

Font styles to use
Sans Serif

Colors

Designer to choose colors to be used in the design.

Requirements
Must have
• Wordpress template, blog and presentation pages, nice background images, incorporate the existing logo from brief
Nice to have
• match the word and ppt existing templates for brightline labs

```html
<!DOCTYPE html>
<html lang="en">
<head>
<meta charset="utf-8">
<title>Brightline Labs</title>
<link href="https://fonts.googleapis.com/css2?family=Montserrat:wght@500;600;700&family=Open+Sans:wght@400;600&display=swap" rel="stylesheet">
<style>
:root{
  --blue:#1479c4;
  --blue-dark:#0d5f9e;
  --ink:#333;
  --muted:#888;
  --light:#f3f3f3;
  --footer:#2e2e2e;
  --footer-dark:#222;
  --white:#fff;
}
*{box-sizing:border-box;margin:0;padding:0}
html,body{width:1200px;height:3116px;overflow:hidden}
body{position:relative;font-family:"Open Sans",Arial,sans-serif;color:var(--ink);background:var(--white)}
h1,h2,h3,h4,.btn,.nav a,.brand{font-family:"Montserrat",Arial,sans-serif}
section,header,footer{position:absolute;left:0;width:1200px}

/* hero */
.hero{top:0;height:620px;background:linear-gradient(135deg,#4c5a66 0%,#2f3a44 45%,#5d6873 100%)}
.hero-photo{position:absolute;inset:0;background:linear-gradient(120deg,rgba(90,110,125,.6),rgba(30,40,50,.7) 50%,rgba(120,130,140,.5))}
.topbar{position:absolute;left:80px;top:20px;width:1040px;height:100px;background:var(--white);display:flex;align-items:center;justify-content:space-between;padding:0 24px}
.brand{display:flex;align-items:center;gap:12px;color:var(--blue);font-weight:700;font-size:26px;line-height:1}
.brand-mark{width:36px;height:36px;background:var(--blue)}
.nav{display:flex;gap:36px}
.nav a{font-size:16px;color:#555;text-decoration:none;font-weight:500;padding-bottom:8px}
.nav a.active{color:var(--blue);border-bottom:3px solid var(--blue)}
.hero-title{position:absolute;top:290px;width:100%;text-align:center;color:var(--white);font-size:52px;font-weight:700;letter-spacing:1px}
.hero-text{position:absolute;top:370px;left:300px;width:600px;text-align:center;color:#e6e6e6;font-size:17px;line-height:1.6}
.arrow{position:absolute;top:330px}
.arrow.left{left:24px}.arrow.right{right:24px}

/* headings */
.section-title{text-align:center;font-size:44px;font-weight:700;color:var(--blue);position:absolute;width:100%}

/* services */
.services{top:620px;height:480px;background:var(--white)}
.services .section-title{top:48px}
.cards{position:absolute;top:132px;left:80px;display:flex;gap:40px}
.card{width:230px;height:268px;background:var(--light);border-bottom:4px solid var(--blue);text-align:center;padding-top:36px}
.card svg{display:block;margin:0 auto 18px}
.card h3{font-family:"Open Sans",Arial,sans-serif;font-size:20px;font-weight:600;color:#444;margin-bottom:10px}
.card p{font-size:13px;color:var(--muted);line-height:1.5;padding:0 22px}

/* about */
.about{top:1100px;height:400px;background:var(--blue);color:var(--white);text-align:center;padding-top:50px}
.about .section-title{position:static;color:var(--white);line-height:1.2;margin-bottom:18px}
.about p{width:680px;margin:0 auto 12px;font-size:13px;line-height:1.7;color:#e2eefa}
.buttons{margin-top:22px;display:flex;justify-content:center;gap:20px}
.btn{background:var(--white);color:var(--blue);font-weight:700;font-size:17px;border-radius:26px;padding:10px 26px}

/* testimonials */
.testimonials{top:1500px;height:500px;background:#3b3f44}
.testimonial-photo{position:absolute;left:0;top:0;width:620px;height:500px;background:linear-gradient(90deg,#8a8e92,#5b6066 60%,#3b3f44)}
.testimonials h2{position:absolute;left:576px;top:112px;color:var(--white);font-size:44px;font-weight:700}
.quote{position:absolute;left:576px;top:180px;width:540px;color:#ddd;font-size:14px;line-height:1.75}
.client{position:absolute;left:576px;top:352px;color:var(--white);font-size:15px;font-weight:600}
.dots{position:absolute;left:576px;top:460px;display:flex;gap:10px}
.dots span{width:14px;height:14px;border:2px solid var(--white);border-radius:50%}
.dots span.on{background:var(--white)}

/* blog */
.blog{top:2000px;height:620px;background:var(--white)}
.blog .section-title{top:52px}
.post{position:absolute;width:500px;height:192px;background:var(--light);display:flex}
.thumb{width:230px;height:192px;flex-shrink:0}
.post-body{padding:22px 20px}
.post h4{font-family:"Open Sans",Arial,sans-serif;font-size:17px;font-weight:400;color:#444;line-height:1.35}
.date{font-size:11px;color:var(--muted);margin:10px 0;display:flex;align-items:center;gap:8px}
.post p{font-size:12px;color:var(--muted);line-height:1.5}

/* footer */
.footer{top:2620px;height:440px;background:var(--footer);color:#ccc}
.contact-box{position:absolute;left:80px;top:80px;width:300px;height:280px;border:1px solid #555;padding:28px 22px}
.contact-box h4{color:var(--white);font-size:17px;font-weight:700;margin-bottom:26px}
.contact-row{display:flex;gap:14px;align-items:flex-start;font-size:13px;margin-bottom:20px;line-height:1.5}
.quote-title{position:absolute;left:452px;top:100px;color:var(--white);font-size:30px;font-weight:700}
.field{position:absolute;left:452px;width:280px;height:44px;background:#3a3a3a;border:1px solid #4a4a4a;color:#999;font-size:13px;padding:12px 14px}
.message{position:absolute;left:748px;top:192px;width:292px;height:140px;background:#3a3a3a;border:1px solid #4a4a4a;color:#999;font-size:13px;padding:12px 14px}
.send{position:absolute;left:1060px;top:192px;width:60px;height:140px;background:var(--blue);display:flex;align-items:center;justify-content:center}
.copyright{position:absolute;top:3060px;left:0;width:1200px;height:56px;background:var(--footer-dark);color:#aaa;font-size:13px;text-align:center;line-height:56px}
</style>
</head>
<body>

<header class="hero">
  <div class="hero-photo" role="img" aria-label="Background photo of a team working with data charts on laptops"></div>
  <div class="topbar">
    <div class="brand"><span class="brand-mark"></span>BRIGHTLINE LABS</div>
    <nav class="nav">
      <a class="active">HOME</a><a>ABOUT</a><a>SERVICES</a><a>BLOG</a><a>CONTACT</a>
    </nav>
  </div>
  <h1 class="hero-title">BRIGHTLINE LABS</h1>
  <p class="hero-text">Lorem Ipsum is simply dummy text of the printing and typesetting industry. Lorem Ipsum has been the industry's standard dummy text ever since.</p>
  <svg class="arrow left" width="20" height="32" viewBox="0 0 20 32"><path d="M16 3 4 16l12 13" fill="none" stroke="#fff" stroke-width="4"/></svg>
  <svg class="arrow right" width="20" height="32" viewBox="0 0 20 32"><path d="M4 3l12 13L4 29" fill="none" stroke="#fff" stroke-width="4"/></svg>
</header>

<section class="services">
  <h2 class="section-title">OUR SERVICES</h2>
  <div class="cards">
    <div class="card">
      <svg width="84" height="70" viewBox="0 0 84 70" fill="none" stroke="#1479c4" stroke-width="4"><circle cx="32" cy="38" r="14"/><circle cx="32" cy="38" r="5"/><path d="M32 18v-6M32 58v6M12 38H6M52 38h6M18 24l-4-4M46 52l4 4M46 24l4-4M18 52l-4 4"/><circle cx="64" cy="18" r="8"/><path d="M64 4v4M64 28v4M50 18h4M74 18h4"/></svg>
      <h3>Machine learning</h3>
      <p>Lorem ipsum dolor sit amet, consectetur adipiscing elit.</p>
    </div>
    <div class="card">
      <svg width="84" height="70" viewBox="0 0 84 70" fill="#1479c4"><rect x="10" y="48" width="10" height="16"/><rect x="26" y="38" width="10" height="26"/><rect x="42" y="26" width="10" height="38"/><rect x="58" y="14" width="10" height="50"/><path d="M8 38 30 22l14 8 24-22" stroke="#1479c4" stroke-width="3" fill="none"/></svg>
      <h3>Big data</h3>
      <p>Lorem ipsum dolor sit amet, consectetur adipiscing elit.</p>
    </div>
    <div class="card">
      <svg width="84" height="70" viewBox="0 0 84 70" fill="none" stroke="#1479c4" stroke-width="3"><ellipse cx="42" cy="35" rx="30" ry="11"/><ellipse cx="42" cy="35" rx="30" ry="11" transform="rotate(60 42 35)"/><ellipse cx="42" cy="35" rx="30" ry="11" transform="rotate(-60 42 35)"/><circle cx="42" cy="35" r="5" fill="#1479c4"/></svg>
      <h3>Data science</h3>
      <p>Lorem ipsum dolor sit amet, consectetur adipiscing elit.</p>
    </div>
    <div class="card">
      <svg width="84" height="70" viewBox="0 0 84 70" fill="none" stroke="#1479c4" stroke-width="4"><circle cx="46" cy="28" r="18"/><path d="M33 41 14 62"/><path d="M36 34l7-8 6 5 7-10" stroke-width="3"/></svg>
      <h3>Data analytics</h3>
      <p>Lorem ipsum dolor sit amet, consectetur adipiscing elit.</p>
    </div>
  </div>
</section>

<section class="about">
  <h2 class="section-title">ABOUT BRIGHTLINE LABS</h2>
  <p>Lorem Ipsum is simply dummy text of the printing and typesetting industry. Lorem Ipsum has been the industry's standard dummy text ever since the 1500s, when an unknown printer took a galley of type and scrambled it to make a type specimen book. It has survived not only five centuries, but also the leap into electronic typesetting.</p>
  <p>Lorem Ipsum is simply dummy text of the printing and typesetting industry. Lorem Ipsum has been the industry's standard dummy text ever since the 1500s, when an unknown printer took a galley of type and scrambled.</p>
  <div class="buttons"><span class="btn">KNOW MORE</span><span class="btn">CONTACT US</span></div>
</section>

<section class="testimonials">
  <div class="testimonial-photo" role="img" aria-label="Photo of a smiling businesswoman in an office"></div>
  <h2>TESTIMONIALS</h2>
  <p class="quote">Lorem Ipsum is simply dummy text of the printing and typesetting industry. Lorem Ipsum has been the industry's standard dummy text ever since the 1500s, when an unknown printer took a galley of type and scrambled it to make a type specimen book. It has survived not only five centuries.</p>
  <p class="client">- CLIENT NAME</p>
  <div class="dots"><span class="on"></span><span></span><span></span><span></span></div>
</section>

<section class="blog">
  <h2 class="section-title">LATEST BLOG</h2>
  <article class="post" style="left:80px;top:120px">
    <div class="thumb" role="img" aria-label="Photo of colleagues meeting around a table" style="background:linear-gradient(135deg,#c9ccd0,#8d949b)"></div>
    <div class="post-body"><h4>Lorem ipsum is simply dummy text of the printing</h4><div class="date"><svg width="12" height="12"><rect x="1" y="2" width="10" height="9" fill="none" stroke="#1479c4" stroke-width="1.5"/></svg>11th April 2017</div><p>Lorem Ipsum is simply dummy text of the printing.</p></div>
  </article>
  <article class="post" style="left:620px;top:120px">
    <div class="thumb" role="img" aria-label="Photo of hands reviewing printed charts" style="background:linear-gradient(135deg,#d8d4cf,#9b9590)"></div>
    <div class="post-body"><h4>Lorem ipsum is simply dummy text of the printing</h4><div class="date"><svg width="12" height="12"><rect x="1" y="2" width="10" height="9" fill="none" stroke="#1479c4" stroke-width="1.5"/></svg>11th April 2017</div><p>Lorem Ipsum is simply dummy text of the printing.</p></div>
  </article>
  <article class="post" style="left:80px;top:352px">
    <div class="thumb" role="img" aria-label="Photo of a team discussing at a desk" style="background:linear-gradient(135deg,#e3e5e8,#a7adb3)"></div>
    <div class="post-body"><h4>Lorem ipsum is simply dummy text of the printing</h4><div class="date"><svg width="12" height="12"><rect x="1" y="2" width="10" height="9" fill="none" stroke="#1479c4" stroke-width="1.5"/></svg>11th April 2017</div><p>Lorem Ipsum is simply dummy text of the printing.</p></div>
  </article>
  <article class="post" style="left:620px;top:352px">
    <div class="thumb" role="img" aria-label="Photo of a business group in a bright meeting room" style="background:linear-gradient(135deg,#bfc5cb,#6e767e)"></div>
    <div class="post-body"><h4>Lorem ipsum is simply dummy text of the printing</h4><div class="date"><svg width="12" height="12"><rect x="1" y="2" width="10" height="9" fill="none" stroke="#1479c4" stroke-width="1.5"/></svg>11th April 2017</div><p>Lorem Ipsum is simply dummy text of the printing.</p></div>
  </article>
</section>

<footer class="footer">
  <div class="contact-box">
    <h4>CONTACT DETAIL</h4>
    <div class="contact-row"><svg width="14" height="20" viewBox="0 0 14 20"><path d="M7 0a7 7 0 0 0-7 7c0 5 7 13 7 13s7-8 7-13a7 7 0 0 0-7-7z" fill="#1479c4"/><circle cx="7" cy="7" r="2.5" fill="#2e2e2e"/></svg><span>Lorem Ipsum is simply dummy text of the printing</span></div>
    <div class="contact-row"><svg width="16" height="16" viewBox="0 0 16 16"><path d="M3 1l3 3-2 2c1 2 3 4 5 5l2-2 3 3-2 3C7 14 2 9 1 3z" fill="#1479c4"/></svg><span>(555) 010 2468</span></div>
    <div class="contact-row"><svg width="16" height="12" viewBox="0 0 16 12"><rect width="16" height="12" fill="#1479c4"/><path d="M0 0l8 6 8-6" fill="none" stroke="#2e2e2e" stroke-width="1.5"/></svg><span>info@brightlinelabs.com</span></div>
  </div>
  <h3 class="quote-title">REQUEST A FREE QUOTE</h3>
  <div class="field" style="top:192px">Name</div>
  <div class="field" style="top:240px">Email</div>
  <div class="field" style="top:288px">Phone</div>
  <div class="message">Message</div>
  <div class="send"><svg width="26" height="26" viewBox="0 0 26 26"><path d="M2 12 24 2 16 24l-4-9z" fill="#fff"/></svg></div>
</footer>
<div class="copyright">©BRIGHTLINE LABS. 2016. All Rights Reserved</div>

</body>
</html>
```